UX - Need some screens design for a Skill Assessment Application

I am building an app to carry out skill assessments. Depending on how the assessment is configured, it may have one or more parts
1. Question based assessment (Multiple Choice, True False, Fill in the blanks"
2. Endorsement by two colleagues - A screen that allows user to pick colleagues based on search and shows the status of pending requests
3. A written submission - a page that explains the format of the submission and a file upload
As each assessment can be configured with or without any of the steps, the assessment UI must be such that these areas get hidden/displayed based on configuration.
Colour codes to be used can be #0e78bb and #ffffff
There will also be a start screen (instructions) and an end screen (results)
Target Market(s)
Enterprise software
Number of Pages Required
4 page

```html
<!DOCTYPE html>
<html lang="en">
<head>
<meta charset="utf-8">
<title>Application Design Capabilities – Assessment</title>
<link rel="stylesheet" href="https://fonts.googleapis.com/css2?family=Inter:wght@400;500;600;700&display=swap">
<style>
  :root {
    --brand-dark: #0053a6;
    --brand: #0e78bb;
    --brand-light: #1ba3de;
    --link: #1b8fd0;
    --white: #ffffff;
    --ink: #262a2e;
    --ink-soft: #55595e;
    --ink-muted: #6b7075;
    --page-bg: #f5f6f8;
    --meta-bg: #f0f1f3;
    --line: #dcdfe3;
    --chip-bg: #cfe9f7;
    --ring-track: #d8dde2;
  }
  * { box-sizing: border-box; margin: 0; padding: 0; }
  html, body { width: 1200px; height: 686px; overflow: hidden; }
  body {
    font-family: "Inter", Arial, sans-serif;
    background: var(--page-bg);
    color: var(--ink);
    position: relative;
  }

  /* Top navigation */
  .top-nav {
    position: absolute; left: 0; top: 0; width: 1200px; height: 43px;
    background: var(--brand-dark);
    display: flex; align-items: center; padding: 0 57px;
    color: var(--white);
  }
  .brand { display: flex; align-items: center; gap: 9px; font-size: 15px; font-weight: 600; }
  .brand-dot { width: 18px; height: 18px; border-radius: 50%; background: var(--white); }
  .nav-links { margin-left: auto; display: flex; gap: 21px; font-size: 12.5px; align-items: center; }
  .nav-links a { color: rgba(255,255,255,.82); text-decoration: none; }
  .nav-links a.active { color: var(--white); font-weight: 600; }
  .account { display: flex; align-items: center; gap: 6px; margin-left: 21px; }
  .avatar { width: 27px; height: 27px; border-radius: 50%; background: linear-gradient(135deg, #5a6f86, #2b3a4c); border: 1px solid rgba(255,255,255,.6); }

  /* Page header */
  .page-head {
    position: absolute; left: 0; top: 43px; width: 1200px; height: 97px;
    background: var(--white); border-bottom: 1px solid var(--line);
  }
  .breadcrumb {
    position: absolute; left: 57px; top: 22px;
    display: flex; align-items: center; gap: 8px; font-size: 11.5px; color: var(--ink-soft);
  }
  .breadcrumb .crumb-link { color: var(--link); margin-left: 5px; }
  .last-updated { position: absolute; right: 88px; top: 25px; font-size: 11.5px; color: var(--ink-soft); }
  .last-updated b { font-weight: 500; color: var(--ink); }
  .page-title {
    position: absolute; left: 88px; top: 55px;
    display: flex; align-items: center; gap: 14px;
    font-size: 20.5px; font-weight: 600; color: var(--ink);
  }
  .btn {
    font-family: inherit; font-size: 11.5px; font-weight: 500;
    border-radius: 3px; display: inline-flex; align-items: center; justify-content: center;
  }
  .btn-outline { background: var(--white); color: var(--brand); border: 1px solid var(--brand); }
  .btn-solid { background: var(--brand); color: var(--white); border: 1px solid var(--brand); }
  .save-progress { position: absolute; right: 88px; top: 53px; width: 104px; height: 31px; }

  /* Assessment meta strip */
  .meta-strip {
    position: absolute; left: 0; top: 140px; width: 1200px; height: 44px;
    background: var(--meta-bg); border-bottom: 1px solid var(--line);
    display: flex; align-items: center; padding-left: 88px; font-size: 10px; color: var(--ink);
  }
  .meta-item { padding-right: 21px; margin-right: 21px; border-right: 1px solid var(--line); line-height: 14px; }
  .meta-item:last-of-type { border-right: 0; }
  .meta-item .value { color: var(--link); }
  .meta-item .note { color: var(--ink-muted); }
  .progress { position: absolute; right: 88px; top: 7px; display: flex; align-items: center; gap: 6px; font-size: 10.5px; color: var(--ink-muted); }
  .progress b { color: var(--ink); font-weight: 600; }

  /* Question */
  .question { position: absolute; left: 366px; top: 217px; width: 468px; }
  .question-title { display: flex; gap: 21px; font-size: 15px; font-weight: 500; height: 22px; align-items: center; }
  .question-title .q-no { color: var(--ink-muted); font-weight: 400; }
  .statements { margin-top: 25px; display: flex; flex-direction: column; gap: 7px; }
  .statement {
    height: 69px; background: var(--white); border-radius: 3px;
    box-shadow: 0 1px 4px rgba(0,0,0,.06);
    display: flex; align-items: center; padding: 0 14px;
  }
  .statement-no {
    width: 31px; height: 27px; background: var(--chip-bg); color: var(--ink-muted);
    display: flex; align-items: center; justify-content: center; font-size: 13.5px;
  }
  .statement-text { margin-left: 21px; font-size: 12px; color: var(--ink-soft); margin-top: -2px; }
  .choices { margin-left: auto; display: flex; gap: 7px; }
  .choice {
    width: 52px; height: 31px; border-radius: 16px; font-size: 11px;
    display: flex; align-items: center; justify-content: center;
    border: 1px solid var(--line); color: var(--brand); background: var(--white);
  }
  .choice.selected { background: var(--brand); border-color: var(--brand); color: var(--white); }

  .question-footer { margin-top: 28px; border-top: 1px solid var(--line); padding-top: 27px; display: flex; align-items: center; }
  .go-back { width: 72px; height: 31px; }
  .skip { margin-left: auto; margin-right: 25px; font-size: 11.5px; color: var(--ink-soft); display: flex; align-items: center; gap: 5px; }
  .next { width: 52px; height: 31px; }
</style>
</head>
<body>

<header class="top-nav">
  <div class="brand"><span class="brand-dot"></span>Assessly</div>
  <nav class="nav-links">
    <a class="active">Assessments</a>
    <a>Endorsement</a>
    <a>Submissions</a>
    <a>Results</a>
  </nav>
  <div class="account">
    <div class="avatar" role="img" aria-label="User profile photo"></div>
    <svg width="10" height="10" viewBox="0 0 10 10"><path d="M2 3.5 5 6.5 8 3.5" fill="none" stroke="#fff" stroke-width="1.4"/></svg>
  </div>
</header>

<section class="page-head">
  <div class="breadcrumb">
    <svg width="19" height="19" viewBox="0 0 19 19"><circle cx="9.5" cy="9.5" r="8.5" fill="none" stroke="#0e78bb" stroke-width="1.6"/><path d="M13.5 9.5H6M9 6 5.5 9.5 9 13" fill="none" stroke="#0e78bb" stroke-width="1.6"/></svg>
    <span class="crumb-link">Assessment</span><span>/</span><span>Application Design Capabilities</span>
  </div>
  <div class="last-updated">Last Updated: <b>17/05/2024</b></div>
  <h1 class="page-title">
    <svg width="21" height="21" viewBox="0 0 21 21" fill="none" stroke="#55595e" stroke-width="1.4"><rect x="1.5" y="1.5" width="13" height="17" rx="1"/><path d="M4.5 6h2M8.5 6h3M4.5 10h2M8.5 10h3M4.5 14h2"/><circle cx="15.5" cy="15.5" r="4" fill="#55595e" stroke="none"/><path d="M13.7 15.5l1.3 1.3 2.3-2.4" stroke="#fff"/></svg>
    Application Design Capabilities
  </h1>
  <button class="btn btn-outline save-progress">Save Progress</button>
</section>

<section class="meta-strip">
  <div class="meta-item">Assessment Date: <span class="value">September 23, 2024</span></div>
  <div class="meta-item">Assessment Type: <span class="value">UI/UX Skill</span></div>
  <div class="meta-item">Assessment Responses: <span class="note">5 of 8 Responded / Closed: in next 4 month</span></div>
  <div class="progress">
    <svg width="31" height="31" viewBox="0 0 31 31"><circle cx="15.5" cy="15.5" r="13" fill="none" stroke="var(--ring-track)" stroke-width="3.5"/><circle cx="15.5" cy="15.5" r="13" fill="none" stroke="var(--brand-light)" stroke-width="3.5" stroke-dasharray="61.3 81.7" transform="rotate(-90 15.5 15.5) scale(1 -1) translate(0 -31)"/></svg>
    <span><b>6</b> / 8</span>
  </div>
</section>

<main class="question">
  <h2 class="question-title"><span class="q-no">Q.6.</span>This is multiple question with T/F choice</h2>
  <div class="statements">
    <div class="statement">
      <span class="statement-no">1</span><span class="statement-text">Lorem ipsum dolor sit amet?</span>
      <div class="choices"><span class="choice selected">True</span><span class="choice">False</span></div>
    </div>
    <div class="statement">
      <span class="statement-no">2</span><span class="statement-text">Lorem ipsum dolor sit amet?</span>
      <div class="choices"><span class="choice">True</span><span class="choice selected">False</span></div>
    </div>
    <div class="statement">
      <span class="statement-no">3</span><span class="statement-text">Lorem ipsum dolor sit amet?</span>
      <div class="choices"><span class="choice selected">True</span><span class="choice">False</span></div>
    </div>
  </div>
  <div class="question-footer">
    <button class="btn btn-outline go-back">Go Back</button>
    <span class="skip">Skip <svg width="7" height="10" viewBox="0 0 7 10"><path d="M1.5 1.5 5 5 1.5 8.5" fill="none" stroke="#55595e" stroke-width="1.4"/></svg></span>
    <button class="btn btn-solid next">Next</button>
  </div>
</main>

</body>
</html>
```